Business Cards Needed for Innovative Healthcare Marketing Company

We are a marketing company focused on healthcare. Our company is all about rebranding yourself renewing your image and generating results. The phoenix stands for "reborn" or "rising" which we provide new brands for our clients we take their old brands and renew it with creativity and innovation. I am looking for a business card with color dimension. I have attached an example of a card I think has the look and feel of what I am trying to accomplish. I like that the card example has black and grey font colors, I like the font placement and the small logo, I really like the use of the colors on the right those are the colors of my logo. My logo is phoenix so maybe incorporating flames similar to that design. I would like the back a solid color maybe red with an opaque version of the logo and website. As a marketing company I am always open to creative liberty!

Target Market(s)

Doctors and business professionals.

Industry/Entity Type

Marketing

Contact Information for Business Card

Valcorne Health Care Marketing
Marla Tenwick- CEO
#(512)638-2974
email-marla@valcorne.com
website- valcorne.com

Font styles to use
Sans Serif

Colors
ec1f27
f37122
ffc214
fbed22
fbf289
f04a50

Requirements
Must have
• The logo and required information
Nice to have
• icons by the information
Should not have
• child like font

```html
<!DOCTYPE html>
<html lang="en">
<head>
<meta charset="utf-8">
<title>Valcorne Health Care Marketing – Business Cards</title>
<link rel="stylesheet" href="https://fonts.googleapis.com/css2?family=Raleway:wght@200;300&family=Arvo:wght@400;700&display=swap">
<style>
  :root {
    --backdrop: #3a2418;
    --card-light: #6e1a20;
    --card-dark: #3a0d12;
    --ink-white: #f4eeee;
    --ink-grey: #a7a2a3;
    --accent-red: #ec1f27;
    --accent-soft-red: #f04a50;
    --flame-orange: #f37122;
    --flame-gold: #ffc214;
  }
  * { margin: 0; padding: 0; box-sizing: border-box; }
  html, body { width: 1200px; height: 913px; overflow: hidden; }
  body { background: var(--backdrop); position: relative; }

  .card {
    position: absolute;
    width: 525px;
    height: 300px;
    border-radius: 3px;
    background: radial-gradient(ellipse at 60% 25%, var(--card-light) 0%, var(--card-dark) 85%);
    box-shadow: 0 18px 40px rgba(0,0,0,.45);
    overflow: hidden;
  }
  .card--front { left: 70px; top: 110px; }
  .card--back  { left: 605px; top: 500px; }

  /* Front */
  .brand-mark {
    position: absolute;
    left: 46px; top: 70px;
    width: 150px; height: 150px;
    border-radius: 50%;
    background: rgba(20,10,10,.55);
  }
  .brand-block {
    position: absolute;
    left: 222px; top: 92px;
    color: var(--ink-white);
    font-family: "Raleway", sans-serif;
  }
  .brand-name {
    font-weight: 200;
    font-size: 50px;
    letter-spacing: 2px;
    line-height: 1;
  }
  .brand-rule {
    height: 1px;
    width: 270px;
    background: var(--ink-grey);
    margin: 8px 0 6px;
  }
  .brand-tagline {
    font-weight: 300;
    font-size: 13px;
    letter-spacing: 2.4px;
    color: var(--ink-grey);
  }
  .brand-web {
    margin-top: 26px;
    margin-left: 56px;
    font-family: "Arvo", serif;
    font-size: 17px;
    color: var(--ink-grey);
  }
  .brand-web .web-name { color: var(--accent-red); }

  /* Back */
  .flame-area {
    position: absolute;
    left: 20px; top: 34px;
    width: 235px; height: 235px;
    border-radius: 50%;
    background: radial-gradient(circle at 60% 70%, var(--flame-gold) 0%, var(--flame-orange) 55%, var(--accent-red) 100%);
    opacity: .85;
  }
  .contact-block {
    position: absolute;
    left: 285px; top: 86px;
    font-family: "Arvo", serif;
    color: var(--ink-white);
  }
  .contact-name { font-size: 21px; font-weight: 700; line-height: 1.1; }
  .contact-name .surname { text-transform: uppercase; }
  .contact-role { font-size: 15px; color: var(--ink-grey); margin-bottom: 16px; }
  .contact-line {
    display: flex; align-items: center; gap: 9px;
    font-size: 14px; margin-bottom: 7px;
  }
  .contact-icon {
    width: 20px; height: 20px; border-radius: 50%;
    background: var(--accent-red);
    display: flex; align-items: center; justify-content: center;
    flex: none;
  }
</style>
</head>
<body>
  <section class="card card--front" aria-label="Card front">
    <div class="brand-mark" aria-hidden="true"></div>
    <div class="brand-block">
      <div class="brand-name">VALCORNE</div>
      <div class="brand-rule"></div>
      <div class="brand-tagline">HEALTHCARE MARKETING</div>
      <div class="brand-web">www.<span class="web-name">valcorne</span>.com</div>
    </div>
  </section>

  <section class="card card--back" aria-label="Card back">
    <div class="flame-area" role="img" aria-label="Large flame-coloured brand decoration in red, orange and gold"></div>
    <div class="contact-block">
      <div class="contact-name">Marla <span class="surname">Tenwick</span></div>
      <div class="contact-role">CEO</div>
      <div class="contact-line">
        <span class="contact-icon">
          <svg width="11" height="11" viewBox="0 0 24 24" aria-hidden="true"><path fill="#fff" d="M6.6 10.8a15.1 15.1 0 0 0 6.6 6.6l2.2-2.2c.3-.3.7-.4 1-.2 1.1.4 2.3.6 3.6.6.6 0 1 .4 1 1V20c0 .6-.4 1-1 1A17 17 0 0 1 3 4c0-.6.4-1 1-1h3.5c.6 0 1 .4 1 1 0 1.3.2 2.5.6 3.6.1.3 0 .7-.2 1z"/></svg>
        </span>
        (512) 638-2974
      </div>
      <div class="contact-line">
        <span class="contact-icon">
          <svg width="11" height="11" viewBox="0 0 24 24" aria-hidden="true"><path fill="#fff" d="M3 5h18v14H3z M3 5l9 7 9-7" stroke="#ec1f27" stroke-width="1.5"/></svg>
        </span>
        marla@valcorne.com
      </div>
    </div>
  </section>
</body>
</html>
```